Architectural firm needs a graphic representation of our Master Planning process

We need an image to convey our 3-phase, 8-step Master Planning process that we utilize when designing plans for schools K-12. What we currently use looks very outdated in both the design and color scheme. We'd like an EPS created that can be scaled without distortion. The files I've attached show the current graphic and an instruction sheet which also contains our colors.

```html
<!DOCTYPE html>
<html lang="en">
<head>
<meta charset="utf-8">
<title>Master Planning Process</title>
<link rel="stylesheet" href="https://fonts.googleapis.com/css2?family=Poppins:wght@400;500;600;700&display=swap">
<style>
  :root {
    --red: #a50a35;
    --blue: #22c3c6;
    --green: #5fd32a;
    --yellow: #fbb928;
    --purple: #7b7bd6;
    --ink: #555558;
    --rail: #cfcfd1;
    --paper: #ffffff;
  }
  html, body { margin: 0; padding: 0; overflow: hidden; background: var(--paper); }
  .canvas { width: 849px; height: 1200px; display: block; }
  text { font-family: 'Poppins', sans-serif; }
  .role-label { font-size: 15px; font-weight: 600; letter-spacing: 1.2px; text-anchor: middle; }
  .badge-letter { font-size: 24px; fill: #fff; text-anchor: middle; dominant-baseline: central; }
  .section-title { font-size: 25px; fill: var(--ink); letter-spacing: 3px; text-anchor: middle; }
  .step-major { font-size: 27px; font-weight: 700; fill: var(--ink); letter-spacing: 4px; }
  .step-minor { font-size: 19px; font-weight: 600; fill: var(--ink); letter-spacing: 2px; }
  .step-side { font-size: 19px; font-weight: 600; fill: var(--ink); }
  .legend-title { font-size: 19px; font-weight: 600; fill: var(--ink); letter-spacing: 0.5px; }
  .legend-text { font-size: 18px; font-weight: 600; letter-spacing: 1.2px; }
  .icon { fill: none; stroke: #fff; stroke-width: 2.6; stroke-linecap: round; stroke-linejoin: round; }
</style>
</head>
<body>
<svg class="canvas" viewBox="0 0 1050 1484" xmlns="http://www.w3.org/2000/svg" role="img" aria-label="Master planning process: roles, steps and areas of responsibility">
  <defs>
    <g id="badge-a"><circle r="21" fill="var(--red)"/><text class="badge-letter">A</text></g>
    <g id="badge-s"><circle r="21" fill="var(--blue)"/><text class="badge-letter">S</text></g>
    <g id="badge-f"><circle r="21" fill="var(--green)"/><text class="badge-letter">F</text></g>
    <g id="team">
      <circle cx="0" cy="0" r="27" fill="none" stroke="var(--red)" stroke-width="2"/>
      <circle cx="54" cy="0" r="27" fill="none" stroke="var(--blue)" stroke-width="2"/>
      <circle cx="108" cy="0" r="27" fill="none" stroke="var(--green)" stroke-width="2"/>
      <circle cx="27" cy="0" r="3" fill="#fff" stroke="var(--red)" stroke-width="1.5"/>
      <circle cx="81" cy="0" r="3" fill="#fff" stroke="var(--blue)" stroke-width="1.5"/>
      <use href="#badge-a" x="0"/>
      <use href="#badge-s" x="54"/>
      <use href="#badge-f" x="108"/>
    </g>
  </defs>

  <!-- Roles feeding into the process -->
  <g class="roles">
    <text class="role-label" x="328" y="124" fill="var(--blue)">SCHOOL</text>
    <use href="#badge-s" x="326" y="151"/>
    <text class="role-label" x="155" y="187" fill="var(--red)">ARCHITECTURAL</text>
    <text class="role-label" x="155" y="202" fill="var(--red)">CONSULTANT</text>
    <use href="#badge-a" x="155" y="231"/>
    <text class="role-label" x="496" y="187" fill="var(--green)">FUNDRAISING</text>
    <text class="role-label" x="496" y="202" fill="var(--green)">CONSULTANT</text>
    <use href="#badge-f" x="496" y="231"/>

    <path d="M190 222 L305 222 Q318 222 318 236 L318 272 L302 272 L302 244 Q302 238 296 238 L190 238 L198 230 Z" fill="var(--red)" opacity="0.75"/>
    <path d="M318 186 L334 192 L334 272 L318 272 Z" fill="var(--blue)" opacity="0.65"/>
    <path d="M462 222 L347 222 Q334 222 334 236 L334 272 L350 272 L350 244 Q350 238 356 238 L462 238 L454 230 Z" fill="var(--green)" opacity="0.75"/>
    <path d="M290 270 L362 270 L326 315 Z" fill="var(--blue)" opacity="0.6"/>
    <path d="M290 270 L326 270 L315 285 Z" fill="var(--red)" opacity="0.45"/>
    <path d="M326 270 L362 270 L337 285 Z" fill="var(--green)" opacity="0.45"/>
    <path d="M314 270 L338 270 L326 284 Z" fill="var(--yellow)" opacity="0.9"/>
  </g>

  <text class="section-title" x="326" y="355">PROCESS</text>
  <text class="section-title" x="830" y="340">AREAS</text>
  <text class="section-title" x="830" y="369">OF RESPONSIBILITY</text>

  <!-- Process rail -->
  <g class="rail" stroke="var(--rail)" stroke-width="6" fill="none">
    <path d="M326 428 L268 525 L326 622 L384 525 Z"/>
    <path d="M326 622 L326 990"/>
  </g>
  <path d="M312 986 L340 986 L326 1026 Z" fill="var(--rail)"/>

  <!-- Steps -->
  <g class="steps">
    <circle cx="326" cy="428" r="41" fill="var(--yellow)"/>
    <g class="icon" transform="translate(326 430)">
      <path d="M-24 0 Q0 -22 24 0 Q0 22 -24 0 Z"/><circle r="8"/><circle r="3"/>
      <path d="M0 -26 V-20 M-14 -22 L-11 -17 M14 -22 L11 -17"/>
    </g>

    <circle cx="268" cy="525" r="41" fill="var(--yellow)"/>
    <g class="icon" transform="translate(268 525)">
      <rect x="-18" y="-16" width="18" height="30"/><rect x="0" y="-26" width="18" height="40"/>
      <path d="M-13 -9 h3 M-6 -9 h3 M-13 -2 h3 M-6 -2 h3 M5 -19 h3 M11 -19 h3 M5 -12 h3 M11 -12 h3"/>
      <circle cx="2" cy="12" r="8" fill="var(--yellow)"/><path d="M8 18 L16 26"/>
    </g>

    <circle cx="384" cy="525" r="41" fill="var(--yellow)"/>
    <g class="icon" transform="translate(384 525)">
      <path d="M-22 -22 H-4 Q-8 -14 0 -14 Q8 -14 4 -22 H22 V-4 Q14 -8 14 0 Q14 8 22 4 V22 H4 Q8 14 0 14 Q-8 14 -4 22 H-22 V4 Q-14 8 -14 0 Q-14 -8 -22 -4 Z"/>
      <path d="M0 -14 V14 M-14 0 H14"/>
    </g>

    <circle cx="326" cy="622" r="41" fill="var(--yellow)"/>
    <g class="icon" transform="translate(326 622)">
      <path d="M-18 -26 H18 Q22 -26 22 -22 V14 Q22 18 18 18 H6 L0 28 L-6 18 H-18 Q-22 18 -22 14 V-22 Q-22 -26 -18 -26 Z"/>
      <path d="M0 -16 V4"/><circle cx="0" cy="10" r="1.2"/>
    </g>

    <circle cx="326" cy="718" r="41" fill="var(--yellow)"/>
    <g class="icon" transform="translate(326 718)">
      <path d="M-6 28 V18 Q-22 12 -22 -4 Q-22 -26 0 -26 Q20 -26 22 -6 L26 4 H20 V12 Q20 18 12 18 H8 V28"/>
      <circle cx="0" cy="-6" r="8"/><path d="M-3 3 V8 H3 V3"/>
    </g>

    <circle cx="326" cy="815" r="41" fill="var(--yellow)"/>
    <g class="icon" transform="translate(326 815)">
      <path d="M-16 -26 H16 V26 L10 20 L4 26 L-4 20 L-10 26 L-16 20 Z"/>
      <path d="M-8 -14 l3 3 l6 -6 M-8 -2 l3 3 l6 -6 M-8 10 l3 3 l6 -6 M4 -12 h6 M4 0 h6 M4 12 h6"/>
    </g>

    <circle cx="326" cy="911" r="41" fill="var(--yellow)"/>
    <g class="icon" transform="translate(326 911)">
      <rect x="-20" y="-24" width="26" height="32"/><rect x="-14" y="-18" width="26" height="34" fill="var(--yellow)"/>
      <path d="M-8 -10 H12 L20 -2 V26 H-8 Z" fill="var(--yellow)"/>
      <path d="M12 -10 V-2 H20 M-2 6 H14 M-2 12 H14 M-2 18 H10"/>
    </g>

    <circle cx="326" cy="1069" r="41" fill="var(--purple)"/>
    <g class="icon" transform="translate(326 1069)">
      <path d="M-6 10 L-12 4 Q-2 -20 22 -22 Q20 2 -4 12 Z"/><circle cx="8" cy="-6" r="4"/>
      <path d="M-10 2 L-18 2 L-12 -6 L-4 -6 M4 12 L4 20 L12 14 L12 6 M-14 14 Q-22 16 -22 24 Q-14 24 -10 18"/>
    </g>
  </g>

  <!-- Step labels -->
  <g class="labels">
    <text class="step-major" x="433" y="438">VISIONING</text>
    <text class="step-side" x="218" y="511" text-anchor="end">PHYSICAL</text>
    <text class="step-side" x="218" y="532" text-anchor="end">CONDITIONS</text>
    <text class="step-side" x="218" y="553" text-anchor="end">ASSESSMENT</text>
    <text class="step-side" x="433" y="511">SPACE</text>
    <text class="step-side" x="433" y="532" letter-spacing="3">NEEDS</text>
    <text class="step-side" x="433" y="553">ASSESSMENT</text>
    <text class="step-minor" x="432" y="629">PROBLEM DEFINED</text>
    <text class="step-minor" x="432" y="725">IDENTIFY SOLUTIONS</text>
    <text class="step-major" x="433" y="825">ASSESS &amp; SELECT</text>
    <text class="step-minor" x="432" y="918">COMPILE REPORT</text>
    <text class="step-major" x="432" y="1079">IMPLEMENT PLAN !</text>
  </g>

  <!-- Areas of responsibility -->
  <g class="responsibility">
    <use href="#team" x="775" y="429"/>
    <use href="#badge-a" x="775" y="525"/>
    <use href="#badge-a" x="775" y="622"/>
    <use href="#badge-a" x="775" y="718"/>
    <use href="#team" x="775" y="815"/>
    <use href="#badge-a" x="775" y="911"/>
    <use href="#team" x="775" y="1069"/>
  </g>

  <!-- Legend -->
  <g class="legend">
    <text class="legend-title" x="168" y="1180">Areas of responsibility colors meaning:</text>
    <circle cx="179" cy="1221" r="10" fill="var(--blue)"/>
    <text class="legend-text" x="206" y="1228" fill="var(--blue)">BLUE</text>
    <text class="legend-text" x="304" y="1228" fill="var(--blue)">: SCHOOL</text>
    <circle cx="179" cy="1270" r="10" fill="var(--red)"/>
    <text class="legend-text" x="206" y="1277" fill="var(--red)">RED</text>
    <text class="legend-text" x="304" y="1277" fill="var(--red)">: ARCHITECTURAL CONSULTANT</text>
    <circle cx="179" cy="1320" r="10" fill="var(--green)"/>
    <text class="legend-text" x="206" y="1327" fill="var(--green)">GREEN</text>
    <text class="legend-text" x="304" y="1327" fill="var(--green)">: FUNDRAISING CONSULTANT</text>
    <use href="#team" transform="translate(186 1369) scale(0.6)"/>
    <text class="legend-text" x="304" y="1376" fill="var(--ink)">: WORKING TOGETHER</text>
  </g>
</svg>
</body>
</html>
```